Maple Roster Business Card for recruitment company

We are looking for a Business Card Design that incorporates our personal details and our busines name and logo. We are a specialized search consultancy that recruit Property and Construction professionals.
We would like a business card that stands out and is appealing to the Construction and Property industry as well.

Target Market(s)

people in the construction and property industry

Contact Information for Business Card

Business Name and logo

Font styles to use
Serif

Colors
0094D4
00A9DD
6FCCEA
C7EBF8
E9F6FB

Requirements
Must have
• Business name and logo as well as contact details
Should not have
• No photos of us please

```html
<!DOCTYPE html>
<html lang="en">
<head>
<meta charset="utf-8">
<title>Maple Roster – Business Card</title>
<link rel="stylesheet" href="https://fonts.googleapis.com/css2?family=Jost:wght@300&family=Source+Sans+3:wght@300;400;700&display=swap">
<style>
  :root {
    --navy: #003a4f;
    --paper: #f4f5f6;
    --backdrop: #e4e5e6;
    --rule: #b9bdc0;
    --text: #2f3b42;
  }
  html, body {
    margin: 0;
    padding: 0;
    width: 1200px;
    height: 1200px;
    overflow: hidden;
    background: var(--backdrop);
  }
  .canvas {
    position: relative;
    width: 1200px;
    height: 1200px;
  }
  .card {
    position: absolute;
    left: 263px;
    width: 682px;
    height: 390px;
    border-radius: 36px;
    overflow: hidden;
    box-shadow: 0 18px 30px rgba(0,0,0,0.12);
  }
  .card--front { top: 165px; background: var(--navy); }
  .card--back { top: 654px; background: var(--paper); }

  .wordmark {
    position: absolute;
    margin: 0;
    font-family: "Jost", sans-serif;
    font-weight: 300;
    letter-spacing: 0.02em;
    white-space: nowrap;
    line-height: 1;
  }
  .card--front .wordmark {
    right: 53px;
    top: 304px;
    font-size: 37px;
    color: #ffffff;
  }
  .card--back .wordmark {
    left: 74px;
    top: 62px;
    font-size: 42px;
    color: var(--navy);
  }

  .divider {
    position: absolute;
    left: 73px;
    right: 73px;
    top: 256px;
    height: 1px;
    background: var(--rule);
  }

  .person {
    position: absolute;
    left: 72px;
    top: 274px;
    font-family: "Source Sans 3", sans-serif;
    color: var(--text);
  }
  .person__name {
    margin: 0 0 2px;
    font-size: 20px;
    font-weight: 700;
    color: var(--navy);
    line-height: 1.1;
  }
  .person__role {
    margin: 0;
    font-size: 15.5px;
    font-weight: 300;
    line-height: 1.3;
  }

  .contact {
    position: absolute;
    right: 73px;
    top: 279px;
    margin: 0;
    padding: 0;
    list-style: none;
    font-family: "Source Sans 3", sans-serif;
    font-weight: 300;
    font-size: 15px;
    color: var(--text);
  }
  .contact__item {
    display: flex;
    align-items: center;
    justify-content: flex-end;
    gap: 8px;
    height: 20px;
  }
  .contact__icon {
    width: 12px;
    height: 12px;
    fill: var(--navy);
    stroke: var(--navy);
  }
</style>
</head>
<body>
<main class="canvas">
  <section class="card card--front" aria-label="Card front">
    <p class="wordmark">MAPLE ROSTER</p>
  </section>

  <section class="card card--back" aria-label="Card back">
    <p class="wordmark">MAPLE ROSTER</p>
    <div class="divider"></div>
    <div class="person">
      <p class="person__name">Clara Whitford</p>
      <p class="person__role">Director</p>
      <p class="person__role">Senior Search Consultant</p>
    </div>
    <ul class="contact">
      <li class="contact__item">+64 27 555 0142
        <svg class="contact__icon" viewBox="0 0 12 12" aria-hidden="true"><path stroke="none" d="M2.4 1 4.2.8 5.2 3.4 4 4.3c.6 1.4 1.6 2.5 3 3.2l1-1.2 2.5 1.1-.2 1.8c-.2.6-.8.9-1.4.8C4.9 9.6 2.2 6.8 1.7 2.4 1.6 1.8 1.9 1.2 2.4 1z"/></svg>
      </li>
      <li class="contact__item">clara@mapleroster.nz
        <svg class="contact__icon" viewBox="0 0 12 12" aria-hidden="true"><rect x="0.5" y="2.5" width="11" height="7" stroke="none"/><path d="M0.8 2.8 6 6.6 11.2 2.8" fill="none" stroke="#f4f5f6" stroke-width="1"/></svg>
      </li>
      <li class="contact__item">www.mapleroster.nz
        <svg class="contact__icon" viewBox="0 0 12 12" aria-hidden="true"><g fill="none" stroke-width="1"><circle cx="6" cy="6" r="5"/><ellipse cx="6" cy="6" rx="2.2" ry="5"/><path d="M1 6h10M1.8 3.5h8.4M1.8 8.5h8.4"/></g></svg>
      </li>
    </ul>
  </section>
</main>
</body>
</html>
```